Popcorn, ice cream, alcohol infused shakes shop

Create a clean simple website with pictures and bold type for a popcorn, ice cream and boozy shake shop. The site should have:
- Unique and Large Typography
- Large & Responsive Hero (stunning, elicits a response) Images.No concern with above or below the fold. Create a strong visual experience that encourages visitors to scroll down to read more. Use large images to visually tell a story without having to rely on just text.
- Flat image designs
- Place for me to upload an ad type video
- Hidden type menu (three line menu)
- A few small card like images (food, gift bags, tins, etc.) menu items with a brief description.

Target Market(s)

21-49 years of age for the boozy shakes. Soccer moms for sports teams & sleepovers, professionals (teachers, realtors, pharm sales), gifts for family and friends. Also some kids

Coding

Coded - Design and coding required

Number of Pages Required

5+ page

Font styles to use
Sans Serif

Colors

Designer to choose colors to be used in the design.

Requirements
Must have
• Images of gourmet popcorn, fancy shakes, ice cream, gift bags and popcorn tins. Holiday popcorn tins and gift bags along with grift certificates. Ability for visitors to send a contact form to kt@treatloft.example
• Five pages - Home Page, AboutUs, Menu, Gift/Promotion, Contact Us
Nice to have
• Smooth flow on the home page. Mostly images and bold text.
Should not have
• Too many words. Boring text fonts

```html
<!DOCTYPE html>
<html lang="en">
<head>
<meta charset="utf-8">
<title>Treat Loft – Website Pages</title>
<link rel="stylesheet" href="https://fonts.googleapis.com/css2?family=Alfa+Slab+One&family=Merriweather:ital,wght@1,700;1,900&family=Poppins:wght@400;500;600;700;800&display=swap">
<style>
:root{
  --sand:#dcc5a8;
  --sand-light:#e7d8c4;
  --map:#ece4d8;
  --red:#d52129;
  --green:#80c241;
  --ink:#2f2119;
  --muted:#6b5646;
  --line:#7a6352;
  --white:#ffffff;
  --cocoa-dark:#2a1a12;
  --cocoa:#5a3a28;
}
*{box-sizing:border-box;margin:0;padding:0}
html,body{width:1200px;height:1157px;overflow:hidden;background:var(--white)}
body{position:relative;font-family:"Poppins",sans-serif;color:var(--ink)}

.page{position:absolute;width:370px;background:var(--sand);overflow:hidden}
.page--home{left:21px;top:21px;height:1127px}
.page--home-popup{left:414px;top:21px;height:1127px}
.page--about{left:807px;top:25px;height:349px}
.page--contact{left:807px;top:394px;height:440px}
.page > *{position:absolute}

/* header */
.brand{left:35px;top:4px;font:800 9px/0.95 "Poppins",sans-serif;color:var(--red);text-transform:uppercase;letter-spacing:.3px}
.phone{left:258px;top:7px;display:flex;align-items:center;gap:4px;font:600 6.4px/1 "Poppins",sans-serif;color:var(--ink);white-space:nowrap}
.phone svg{width:11px;height:11px}
.burger{left:327px;top:23px;width:9px;height:8px;display:flex;flex-direction:column;justify-content:space-between}
.burger i{display:block;height:1.6px;background:var(--ink)}

/* section headings */
.heading{left:0;width:100%;text-align:center;font:400 14px/1 "Alfa Slab One",serif;letter-spacing:.2px;white-space:nowrap}
.heading .r{color:var(--red)}
.heading .g{color:var(--green)}
.dots{left:149px;width:72px;border-top:1.2px dotted var(--line)}
.trio{left:170px;width:30px;height:10px}
.lede{left:95px;width:180px;text-align:center;font:500 4.3px/8.7px "Poppins",sans-serif;color:var(--ink)}

/* photo placeholders */
.hero-photo{left:0;top:111px;width:370px;height:133px;background:radial-gradient(ellipse at 60% 55%,#6b3f28 0%,#a7764e 30%,#cfa97c 55%,rgba(220,197,168,0) 80%)}
.arrow{width:11px;height:11px;border:1px solid var(--ink);border-radius:50%;display:flex;align-items:center;justify-content:center}
.arrow svg{width:5px;height:5px}
.arrow--prev{left:18px;top:128px}
.arrow--next{right:18px;top:128px}

.about-col{left:34px;width:136px;text-align:center}
.about-title{font:900 8px/1 "Merriweather",serif;font-style:italic;color:var(--ink)}
.about-tag{margin-top:5px;font:700 4.2px/1 "Merriweather",serif;font-style:italic;color:var(--ink)}
.about-copy{margin-top:4px;font:400 4.3px/8.7px "Poppins",sans-serif;color:var(--muted)}
.learn{margin-top:6px;font:700 4.5px/1 "Poppins",sans-serif;color:var(--red);display:inline-flex;align-items:center;gap:2px}
.learn i{display:inline-block;width:4px;height:4px;border-radius:50%;border:.8px solid var(--red)}
.treats-photo{left:180px;top:291px;width:170px;height:99px;border-radius:40px;background:radial-gradient(ellipse at 30% 55%,#6c3a22 0%,#b87e4d 35%,rgba(220,197,168,0) 70%),radial-gradient(ellipse at 75% 45%,#efe3cf 0%,rgba(220,197,168,0) 60%)}

.video-band{left:0;top:405px;width:370px;height:147px;background:linear-gradient(90deg,#3a2418 0%,#6a4430 30%,#3b261a 60%,#1f140e 100%)}
.video-band .play{position:absolute;left:256px;top:36px;width:24px;height:24px;border:1.5px solid var(--white);border-radius:50%}
.video-band .play svg{position:absolute;left:8px;top:6.5px;width:9px;height:9px}
.band-title{position:absolute;left:190px;width:158px;top:69px;text-align:center;font:400 8.6px/1 "Alfa Slab One",serif;color:var(--white);white-space:nowrap}
.band-sub{position:absolute;left:190px;width:158px;top:83px;text-align:center;font:700 4.3px/1 "Merriweather",serif;font-style:italic;color:var(--white);white-space:nowrap}
.btn-red{position:absolute;background:var(--red);color:var(--white);font:700 4.6px/1 "Poppins",sans-serif;display:flex;align-items:center;justify-content:center;white-space:nowrap}
.video-band .btn-red{left:243px;top:96px;width:52px;height:12px}

.features{left:0;top:622px;width:370px;height:70px}
.feature{position:absolute;width:76px;margin-left:-38px;text-align:center}
.feature .ring{width:34px;height:34px;margin:0 auto;border:1px solid var(--red);border-radius:50%;display:flex;align-items:center;justify-content:center}
.feature .ring svg{width:18px;height:18px}
.feature h4{margin-top:4px;font:700 5px/8px "Merriweather",serif;font-style:italic;color:var(--ink)}
.feature p{margin-top:2px;font:400 4px/8px "Poppins",sans-serif;color:var(--muted)}

.holiday-band{left:0;top:715px;width:370px;height:133px;background:linear-gradient(120deg,#2d1d16 0%,#4a3024 45%,#3a2a22 70%,#5b6a3a 100%)}
.holiday-copy{position:absolute;left:110px;width:150px;top:96px;text-align:center;font:700 4.4px/8px "Merriweather",serif;font-style:italic;color:var(--white)}

.map{left:0;width:370px;background:var(--map)}
.page--home .map,.page--home-popup .map{top:848px;height:115px}

.contact-box{background:var(--green)}
.page--home .contact-box,.page--home-popup .contact-box{left:60px;top:918px;width:250px;height:122px}
.info-card{position:absolute;left:12px;top:13px;width:105px;height:95px;background:#f7f5f2;text-align:center}
.info-card h3{margin-top:13px;font:400 8px/1 "Alfa Slab One",serif;color:var(--ink);white-space:nowrap}
.info-card .name{margin-top:5px;font:700 4.8px/1 "Poppins",sans-serif;color:var(--red);text-transform:uppercase}
.info-card p{font:400 4.4px/8.6px "Poppins",sans-serif;color:var(--ink)}
.info-card .addr{margin-top:2px}
.info-card .ico{display:inline-block;width:4px;height:4px;border:.7px solid var(--green);border-radius:50%;margin-right:2px;vertical-align:-.3px}
.form{position:absolute;left:129px;top:12px;width:109px}
.form h3{font:400 8px/1 "Alfa Slab One",serif;color:var(--white);white-space:nowrap}
.field{margin-top:6px;height:8px;border-bottom:.6px solid var(--white);font:400 3.8px/1 "Poppins",sans-serif;color:var(--white)}
.field:first-of-type{margin-top:7px}
.field--msg{height:20px}
.submit{margin-top:7px;width:43px;height:11px;border:.8px solid var(--white);color:var(--white);font:700 4.4px/1 "Poppins",sans-serif;display:flex;align-items:center;justify-content:center}

.footer-brand{left:0;width:100%;text-align:center;font:800 16px/0.95 "Poppins",sans-serif;color:var(--red);text-transform:uppercase}
.footer-nav{left:0;width:100%;display:flex;justify-content:center;gap:12px;font:500 4.8px/1 "Poppins",sans-serif;color:var(--ink);white-space:nowrap}
.copyright{left:0;width:100%;text-align:center;font:400 3.8px/1 "Poppins",sans-serif;color:var(--ink)}

/* popup state */
.dim{left:0;top:0;width:100%;height:100%;background:rgba(20,12,8,.52)}
.modal{left:83px;top:63px;width:203px;height:108px;overflow:hidden;text-align:center}
.modal-photo{position:absolute;inset:0;background:linear-gradient(160deg,#c9c2bb 0%,#a89d95 45%,#8a7f78 100%)}
.modal .brand-mark{position:absolute;left:0;width:100%;top:9px;font:800 10px/0.95 "Poppins",sans-serif;color:var(--red);text-transform:uppercase}
.modal .offer{position:absolute;left:30px;width:143px;top:41px;font:700 6.4px/8.6px "Poppins",sans-serif;color:var(--white)}
.modal .email{position:absolute;left:28px;top:64px;width:142px;height:11px;border-radius:6px;background:var(--white);text-align:left;padding-left:7px;font:400 3.8px/11px "Poppins",sans-serif;color:#888}
.modal .btn-red{left:67px;top:82px;width:70px;height:12px;border-radius:6px;font-size:4.2px}
.modal .close{position:absolute;right:6px;top:4px;font:700 7px/1 "Poppins",sans-serif;color:var(--white)}

/* about page */
.page--about .about-col{left:35px;width:135px;top:90px;text-align:left}
.page--about .about-copy{text-align:justify;margin-top:4px}
.about-photo{left:176px;top:111px;width:168px;height:93px;border-radius:40px;background:radial-gradient(ellipse at 30% 55%,#6c3a22 0%,#b87e4d 35%,rgba(220,197,168,0) 70%),radial-gradient(ellipse at 75% 45%,#efe3cf 0%,rgba(220,197,168,0) 60%)}
.about-full{left:35px;top:220px;width:308px;text-align:justify;font:400 4.3px/8.7px "Poppins",sans-serif;color:var(--muted)}
.subline{left:0;width:100%;text-align:center;font:600 5px/1 "Poppins",sans-serif;color:var(--ink)}

/* contact page */
.channels{left:0;top:77px;width:370px;height:70px}
.channel{position:absolute;width:90px;margin-left:-45px;text-align:center}
.channel .ring{width:24px;height:24px;margin:0 auto;border:1px solid var(--red);border-radius:50%;display:flex;align-items:center;justify-content:center}
.channel .ring svg{width:11px;height:11px}
.channel h4{margin-top:6px;font:700 5px/1 "Merriweather",serif;font-style:italic;color:var(--ink)}
.channel p{margin-top:4px;font:400 4.4px/8.6px "Poppins",sans-serif;color:var(--ink)}
.page--contact .map{top:158px;height:116px}
.page--contact .contact-box{left:62px;top:228px;width:249px;height:123px}
</style>
</head>
<body>

<!-- HOME -->
<section class="page page--home">
  <div class="brand">Treat<br>Loft</div>
  <div class="phone"><svg viewBox="0 0 12 12"><circle cx="6" cy="6" r="5.4" fill="none" stroke="#d52129" stroke-width="0.9"/><path d="M4 3.2c.4-.3.7-.2.9.2l.5 1c.1.3 0 .5-.2.7l-.3.3c.3.7.9 1.3 1.6 1.6l.3-.3c.2-.2.4-.3.7-.2l1 .5c.4.2.5.5.2.9-.5.7-1.3.9-2.2.4-1.3-.7-2.3-1.7-3-3-.4-.9-.2-1.6.5-2.1z" fill="#d52129"/></svg>(555) 014-2290</div>
  <div class="burger"><i></i><i></i><i></i></div>

  <h1 class="heading" style="font-size:16px;top:45px"><span class="r">TREAT</span> <span class="g">LOFT</span></h1>
  <div class="dots" style="top:66px"></div>
  <svg class="trio" style="top:72px" viewBox="0 0 30 10" role="img" aria-label="Popcorn, cone and shake icons"><g fill="none" stroke="#6b5140" stroke-width=".6"><path d="M2 3.5h6l-1 6H3z"/><path d="M2.5 3.5c0-1.5 1.5-2.5 2.5-1.5 1-1 2.5 0 2.5 1.5"/><circle cx="15" cy="3" r="2.2"/><path d="M12.8 4h4.4L15 9.5z"/><path d="M21.5 2h5l-1 7.5h-3z"/><path d="M25 2l1.2-1.8"/></g></svg>
  <p class="lede" style="top:90px">Lorem ipsum dolor sit amet, consectetur adipiscing elit, sed do eiusmod tempor incididunt ut labore et dolore magna aliqua</p>
  <div class="hero-photo" role="img" aria-label="Hero photo: sundae with chocolate drizzle, cola glasses being poured and a bowl of caramel popcorn"></div>
  <div class="arrow arrow--prev"><svg viewBox="0 0 6 6"><path d="M4 1L2 3l2 2" fill="none" stroke="#2f2119" stroke-width=".9"/></svg></div>
  <div class="arrow arrow--next"><svg viewBox="0 0 6 6"><path d="M2 1l2 2-2 2" fill="none" stroke="#2f2119" stroke-width=".9"/></svg></div>

  <h2 class="heading" style="top:250px"><span class="r">ABOUT</span> <span class="g">US</span></h2>
  <svg class="trio" style="top:272px" viewBox="0 0 30 10" role="img" aria-label="Popcorn, cone and shake icons"><g fill="none" stroke="#6b5140" stroke-width=".6"><path d="M2 3.5h6l-1 6H3z"/><path d="M2.5 3.5c0-1.5 1.5-2.5 2.5-1.5 1-1 2.5 0 2.5 1.5"/><circle cx="15" cy="3" r="2.2"/><path d="M12.8 4h4.4L15 9.5z"/><path d="M21.5 2h5l-1 7.5h-3z"/><path d="M25 2l1.2-1.8"/></g></svg>
  <div class="about-col" style="top:292px">
    <div class="about-title">Treat Loft</div>
    <div class="about-tag">Lorem ipsum dolor sit amet, consectetur adipiscing elit</div>
    <p class="about-copy">Lorem ipsum dolor sit amet, consectetur adipiscing elit, sed do eiusmod tempor incididunt ut labore et dolore magna aliqua. Quis ipsum suspendisse ultrices gravida. Risus commodo viverra maecenas accumsan lacus vel facilisis. Lorem ipsum dolor sit amet.</p>
    <div class="learn">LEARN MORE <i></i></div>
  </div>
  <div class="treats-photo" role="img" aria-label="Photo: ice cream scoops with chocolate drizzle, a milkshake and a bowl of popcorn"></div>

  <div class="video-band" role="img" aria-label="Video cover: two chocolate shakes in mason jars on a dark wooden table">
    <div class="play"><svg viewBox="0 0 9 9"><path d="M1.5 0.5l7 4-7 4z" fill="#fff"/></svg></div>
    <div class="band-title">ONLY THE BEST FOR YOU</div>
    <div class="band-sub">Our employees are happy to fulfill any request you may have.</div>
    <div class="btn-red">SEE OUR MENU</div>
  </div>

  <h2 class="heading" style="top:584px"><span class="r">ALL FOR YOUR</span> <span class="g">ENJOYMENT</span></h2>
  <svg class="trio" style="top:604px" viewBox="0 0 30 10" role="img" aria-label="Popcorn, cone and shake icons"><g fill="none" stroke="#6b5140" stroke-width=".6"><path d="M2 3.5h6l-1 6H3z"/><path d="M2.5 3.5c0-1.5 1.5-2.5 2.5-1.5 1-1 2.5 0 2.5 1.5"/><circle cx="15" cy="3" r="2.2"/><path d="M12.8 4h4.4L15 9.5z"/><path d="M21.5 2h5l-1 7.5h-3z"/><path d="M25 2l1.2-1.8"/></g></svg>
  <div class="features">
    <div class="feature" style="left:68px"><div class="ring"><svg viewBox="0 0 18 18"><g fill="none" stroke="#80c241" stroke-width=".9"><path d="M5 4h8l-1.2 12H6.2z"/><path d="M5.4 8h7.2"/><path d="M10 4l2-3"/></g></svg></div><h4>Delicious shakes and<br>boozy shakes</h4><p>Ask our employees and have your order packed up to take home</p></div>
    <div class="feature" style="left:154px"><div class="ring"><svg viewBox="0 0 18 18"><path d="M11 2.5a6.5 6.5 0 1 0 4.5 10.5A5.5 5.5 0 0 1 11 2.5z" fill="none" stroke="#80c241" stroke-width=".9"/></svg></div><h4>For early birds and<br>night owls</h4><p>We are open from 10:30 am to late evening</p></div>
    <div class="feature" style="left:229px"><div class="ring"><svg viewBox="0 0 18 18"><g fill="none" stroke="#80c241" stroke-width=".9"><path d="M9 3a4 4 0 0 1 4 4v4l1.5 2h-11L5 11V7a4 4 0 0 1 4-4z"/><path d="M7.5 14.5a1.5 1.5 0 0 0 3 0"/><path d="M9 1.5V3"/></g></svg></div><h4>Made fresh<br>daily</h4><p>We make our popcorn fresh</p></div>
    <div class="feature" style="left:304px"><div class="ring"><svg viewBox="0 0 18 18"><g fill="none" stroke="#80c241" stroke-width=".9"><path d="M3 14c0-6 4-10 11-10 0 7-4 11-10 11z"/><path d="M3 15l8-8"/></g></svg></div><h4>Also for<br>vegans</h4><p>We also offer non-dairy shakes for our vegan guests</p></div>
  </div>

  <div class="holiday-band" role="img" aria-label="Holiday banner photo: chocolate ice cream with cones, hand-lettered Happy Holiday and a cartoon Santa">
    <p class="holiday-copy">Lorem ipsum dolor sit amet, consectetur adipiscing elit, sed do eiusmod tempor incididunt ut labore et dolore magna aliqua</p>
  </div>

  <div class="map" role="img" aria-label="Street map around the shop location"></div>
  <div class="contact-box">
    <div class="info-card">
      <h3>CONTACT INFO</h3>
      <div class="name">Treat Loft</div>
      <p class="addr">820 Maple Crest Ave #14, Fairview<br>TX 70010,</p>
      <p><span class="ico"></span>(555) 014-2290</p>
      <p><span class="ico"></span>Mon - Thu10:30 - 9:00</p>
      <p>Fri - Sat10:30 - 10:30</p>
      <p>Sunday11:00 - 8:00</p>
    </div>
    <div class="form">
      <h3>GET IN TOUCH</h3>
      <div class="field">Name</div>
      <div class="field">Email Address</div>
      <div class="field">Phone No</div>
      <div class="field field--msg">Message</div>
      <div class="submit">SUBMIT</div>
    </div>
  </div>

  <div class="footer-brand" style="top:1058px">Treat<br>Loft</div>
  <nav class="footer-nav" style="top:1105px"><span>HOME</span><span>ABOUTUS</span><span>MENU</span><span>GIFT/PROMOTION</span><span>CONTACT US</span></nav>
  <p class="copyright" style="top:1118px">Copyright © 2019. All Rights Reserved Privacy Policy | Term of Use</p>
</section>

<!-- HOME WITH COUPON POPUP -->
<section class="page page--home-popup">
  <div class="brand">Treat<br>Loft</div>
  <div class="phone"><svg viewBox="0 0 12 12"><circle cx="6" cy="6" r="5.4" fill="none" stroke="#d52129" stroke-width="0.9"/><path d="M4 3.2c.4-.3.7-.2.9.2l.5 1c.1.3 0 .5-.2.7l-.3.3c.3.7.9 1.3 1.6 1.6l.3-.3c.2-.2.4-.3.7-.2l1 .5c.4.2.5.5.2.9-.5.7-1.3.9-2.2.4-1.3-.7-2.3-1.7-3-3-.4-.9-.2-1.6.5-2.1z" fill="#d52129"/></svg>(555) 014-2290</div>
  <div class="burger"><i></i><i></i><i></i></div>

  <h1 class="heading" style="font-size:16px;top:45px"><span class="r">TREAT</span> <span class="g">LOFT</span></h1>
  <div class="dots" style="top:66px"></div>
  <svg class="trio" style="top:72px" viewBox="0 0 30 10" role="img" aria-label="Popcorn, cone and shake icons"><g fill="none" stroke="#6b5140" stroke-width=".6"><path d="M2 3.5h6l-1 6H3z"/><path d="M2.5 3.5c0-1.5 1.5-2.5 2.5-1.5 1-1 2.5 0 2.5 1.5"/><circle cx="15" cy="3" r="2.2"/><path d="M12.8 4h4.4L15 9.5z"/><path d="M21.5 2h5l-1 7.5h-3z"/><path d="M25 2l1.2-1.8"/></g></svg>
  <p class="lede" style="top:90px">Lorem ipsum dolor sit amet, consectetur adipiscing elit, sed do eiusmod tempor incididunt ut labore et dolore magna aliqua</p>
  <div class="hero-photo" role="img" aria-label="Hero photo: sundae with chocolate drizzle, cola glasses being poured and a bowl of caramel popcorn"></div>
  <div class="arrow arrow--prev"><svg viewBox="0 0 6 6"><path d="M4 1L2 3l2 2" fill="none" stroke="#2f2119" stroke-width=".9"/></svg></div>
  <div class="arrow arrow--next"><svg viewBox="0 0 6 6"><path d="M2 1l2 2-2 2" fill="none" stroke="#2f2119" stroke-width=".9"/></svg></div>

  <h2 class="heading" style="top:250px"><span class="r">ABOUT</span> <span class="g">US</span></h2>
  <svg class="trio" style="top:272px" viewBox="0 0 30 10" role="img" aria-label="Popcorn, cone and shake icons"><g fill="none" stroke="#6b5140" stroke-width=".6"><path d="M2 3.5h6l-1 6H3z"/><path d="M2.5 3.5c0-1.5 1.5-2.5 2.5-1.5 1-1 2.5 0 2.5 1.5"/><circle cx="15" cy="3" r="2.2"/><path d="M12.8 4h4.4L15 9.5z"/><path d="M21.5 2h5l-1 7.5h-3z"/><path d="M25 2l1.2-1.8"/></g></svg>
  <div class="about-col" style="top:292px">
    <div class="about-title">Treat Loft</div>
    <div class="about-tag">Lorem ipsum dolor sit amet, consectetur adipiscing elit</div>
    <p class="about-copy">Lorem ipsum dolor sit amet, consectetur adipiscing elit, sed do eiusmod tempor incididunt ut labore et dolore magna aliqua. Quis ipsum suspendisse ultrices gravida. Risus commodo viverra maecenas accumsan lacus vel facilisis. Lorem ipsum dolor sit amet.</p>
    <div class="learn">LEARN MORE <i></i></div>
  </div>
  <div class="treats-photo" role="img" aria-label="Photo: ice cream scoops with chocolate drizzle, a milkshake and a bowl of popcorn"></div>

  <div class="video-band" role="img" aria-label="Video cover: two chocolate shakes in mason jars on a dark wooden table">
    <div class="play"><svg viewBox="0 0 9 9"><path d="M1.5 0.5l7 4-7 4z" fill="#fff"/></svg></div>
    <div class="band-title">ONLY THE BEST FOR YOU</div>
    <div class="band-sub">Our employees are happy to fulfill any request you may have.</div>
    <div class="btn-red">SEE OUR MENU</div>
  </div>

  <h2 class="heading" style="top:584px"><span class="r">ALL FOR YOUR</span> <span class="g">ENJOYMENT</span></h2>
  <svg class="trio" style="top:604px" viewBox="0 0 30 10" role="img" aria-label="Popcorn, cone and shake icons"><g fill="none" stroke="#6b5140" stroke-width=".6"><path d="M2 3.5h6l-1 6H3z"/><path d="M2.5 3.5c0-1.5 1.5-2.5 2.5-1.5 1-1 2.5 0 2.5 1.5"/><circle cx="15" cy="3" r="2.2"/><path d="M12.8 4h4.4L15 9.5z"/><path d="M21.5 2h5l-1 7.5h-3z"/><path d="M25 2l1.2-1.8"/></g></svg>
  <div class="features">
    <div class="feature" style="left:68px"><div class="ring"><svg viewBox="0 0 18 18"><g fill="none" stroke="#80c241" stroke-width=".9"><path d="M5 4h8l-1.2 12H6.2z"/><path d="M5.4 8h7.2"/><path d="M10 4l2-3"/></g></svg></div><h4>Delicious shakes and<br>boozy shakes</h4><p>Ask our employees and have your order packed up to take home</p></div>
    <div class="feature" style="left:154px"><div class="ring"><svg viewBox="0 0 18 18"><path d="M11 2.5a6.5 6.5 0 1 0 4.5 10.5A5.5 5.5 0 0 1 11 2.5z" fill="none" stroke="#80c241" stroke-width=".9"/></svg></div><h4>For early birds and<br>night owls</h4><p>We are open from 10:30 am to late evening</p></div>
    <div class="feature" style="left:229px"><div class="ring"><svg viewBox="0 0 18 18"><g fill="none" stroke="#80c241" stroke-width=".9"><path d="M9 3a4 4 0 0 1 4 4v4l1.5 2h-11L5 11V7a4 4 0 0 1 4-4z"/><path d="M7.5 14.5a1.5 1.5 0 0 0 3 0"/><path d="M9 1.5V3"/></g></svg></div><h4>Made fresh<br>daily</h4><p>We make our popcorn fresh</p></div>
    <div class="feature" style="left:304px"><div class="ring"><svg viewBox="0 0 18 18"><g fill="none" stroke="#80c241" stroke-width=".9"><path d="M3 14c0-6 4-10 11-10 0 7-4 11-10 11z"/><path d="M3 15l8-8"/></g></svg></div><h4>Also for<br>vegans</h4><p>We also offer non-dairy shakes for our vegan guests</p></div>
  </div>

  <div class="holiday-band" role="img" aria-label="Holiday banner photo: chocolate ice cream with cones, hand-lettered Happy Holiday and a cartoon Santa">
    <p class="holiday-copy">Lorem ipsum dolor sit amet, consectetur adipiscing elit, sed do eiusmod tempor incididunt ut labore et dolore magna aliqua</p>
  </div>

  <div class="map" role="img" aria-label="Street map around the shop location"></div>
  <div class="contact-box">
    <div class="info-card">
      <h3>CONTACT INFO</h3>
      <div class="name">Treat Loft</div>
      <p class="addr">820 Maple Crest Ave #14, Fairview<br>TX 70010,</p>
      <p><span class="ico"></span>(555) 014-2290</p>
      <p><span class="ico"></span>Mon - Thu10:30 - 9:00</p>
      <p>Fri - Sat10:30 - 10:30</p>
      <p>Sunday11:00 - 8:00</p>
    </div>
    <div class="form">
      <h3>GET IN TOUCH</h3>
      <div class="field">Name</div>
      <div class="field">Email Address</div>
      <div class="field">Phone No</div>
      <div class="field field--msg">Message</div>
      <div class="submit">SUBMIT</div>
    </div>
  </div>

  <div class="footer-brand" style="top:1058px">Treat<br>Loft</div>
  <nav class="footer-nav" style="top:1105px"><span>HOME</span><span>ABOUTUS</span><span>MENU</span><span>GIFT/PROMOTION</span><span>CONTACT US</span></nav>
  <p class="copyright" style="top:1118px">Copyright © 2019. All Rights Reserved Privacy Policy | Term of Use</p>

  <div class="dim"></div>
  <div class="modal">
    <div class="modal-photo" role="img" aria-label="Photo: hands holding a bowl of popcorn"></div>
    <div class="brand-mark">Treat<br>Loft</div>
    <p class="offer">Save 10% on your First order on your favorite snack</p>
    <div class="email">Type Your Email</div>
    <div class="btn-red">GET MY COUPON</div>
    <span class="close">×</span>
  </div>
</section>

<!-- ABOUT US -->
<section class="page page--about">
  <div class="brand">Treat<br>Loft</div>
  <div class="phone"><svg viewBox="0 0 12 12"><circle cx="6" cy="6" r="5.4" fill="none" stroke="#d52129" stroke-width="0.9"/><path d="M4 3.2c.4-.3.7-.2.9.2l.5 1c.1.3 0 .5-.2.7l-.3.3c.3.7.9 1.3 1.6 1.6l.3-.3c.2-.2.4-.3.7-.2l1 .5c.4.2.5.5.2.9-.5.7-1.3.9-2.2.4-1.3-.7-2.3-1.7-3-3-.4-.9-.2-1.6.5-2.1z" fill="#d52129"/></svg>(555) 014-2290</div>
  <div class="burger"><i></i><i></i><i></i></div>

  <h1 class="heading" style="top:29px;font-size:11px"><span class="r">ABOUT</span> <span class="g">US</span></h1>
  <p class="subline" style="top:44px">(POPCORN, ICE CREAM, &amp; SHAKES)</p>
  <div class="dots" style="top:56px"></div>
  <svg class="trio" style="top:64px" viewBox="0 0 30 10" role="img" aria-label="Popcorn, cone and shake icons"><g fill="none" stroke="#6b5140" stroke-width=".6"><path d="M2 3.5h6l-1 6H3z"/><path d="M2.5 3.5c0-1.5 1.5-2.5 2.5-1.5 1-1 2.5 0 2.5 1.5"/><circle cx="15" cy="3" r="2.2"/><path d="M12.8 4h4.4L15 9.5z"/><path d="M21.5 2h5l-1 7.5h-3z"/><path d="M25 2l1.2-1.8"/></g></svg>
  <div class="about-col">
    <div class="about-title">Treat Loft</div>
    <div class="about-tag">Lorem ipsum dolor sit amet, consectetur adipiscing elit</div>
    <p class="about-copy">Lorem ipsum dolor sit amet, consectetur adipiscing elit, sed do eiusmod tempor incididunt ut labore et dolore magna aliqua. Quis ipsum suspendisse ultrices gravida. Risus commodo viverra maecenas accumsan lacus vel facilisis. Lorem ipsum dolor sit amet, consectetur adipiscing elit, sed do eiusmod tempor incididunt ut labore et dolore magna aliqua. Quis ipsum suspendisse ultrices gravida. Risus commodo viverra maecenas accumsan lacus vel facilisis. Lorem ipsum dolor sit amet, Quis ipsum suspendisse commodo</p>
  </div>
  <div class="about-photo" role="img" aria-label="Photo: ice cream scoops with chocolate drizzle, a milkshake and a bowl of popcorn"></div>
  <p class="about-full">Lorem ipsum dolor sit amet, consectetur adipiscing elit, sed do eiusmod tempor incididunt ut labore et dolore magna aliqua. Quis ipsum suspendisse ultrices gravida. Risus commodo viverra maecenas accumsan lacus vel facilisis. Lorem ipsum dolor sit amet, Lorem ipsum dolor sit amet, consectetur adipiscing elit, sed do eiusmod tempor incididunt ut labore et dolore magna aliqua. Quis ipsum suspendisse ultrices gravida. Risus commodo viverra maecenas accumsan lacus vel facilisis. Lorem ipsum dolor sit amet, Lorem ipsum dolor sit amet, consectetur adipiscing elit, sed do eiusmod tempor incididunt ut labore et dolore magna aliqua. Quis ipsum suspendisse ultrices gravida. Risus commodo viverra maecenas accumsan lacus vel facilisis.</p>

  <div class="footer-brand" style="top:275px">Treat<br>Loft</div>
  <nav class="footer-nav" style="top:322px"><span>HOME</span><span>ABOUTUS</span><span>MENU</span><span>GIFT/PROMOTION</span><span>CONTACT US</span></nav>
  <p class="copyright" style="top:335px">Copyright © 2019. All Rights Reserved Privacy Policy | Term of Use</p>
</section>

<!-- CONTACT US -->
<section class="page page--contact">
  <div class="brand">Treat<br>Loft</div>
  <div class="phone"><svg viewBox="0 0 12 12"><circle cx="6" cy="6" r="5.4" fill="none" stroke="#d52129" stroke-width="0.9"/><path d="M4 3.2c.4-.3.7-.2.9.2l.5 1c.1.3 0 .5-.2.7l-.3.3c.3.7.9 1.3 1.6 1.6l.3-.3c.2-.2.4-.3.7-.2l1 .5c.4.2.5.5.2.9-.5.7-1.3.9-2.2.4-1.3-.7-2.3-1.7-3-3-.4-.9-.2-1.6.5-2.1z" fill="#d52129"/></svg>(555) 014-2290</div>
  <div class="burger"><i></i><i></i><i></i></div>

  <h1 class="heading" style="top:29px;font-size:11px"><span class="r">CONTACT</span> <span class="g">US</span></h1>
  <div class="dots" style="top:46px"></div>
  <svg class="trio" style="top:54px" viewBox="0 0 30 10" role="img" aria-label="Popcorn, cone and shake icons"><g fill="none" stroke="#6b5140" stroke-width=".6"><path d="M2 3.5h6l-1 6H3z"/><path d="M2.5 3.5c0-1.5 1.5-2.5 2.5-1.5 1-1 2.5 0 2.5 1.5"/><circle cx="15" cy="3" r="2.2"/><path d="M12.8 4h4.4L15 9.5z"/><path d="M21.5 2h5l-1 7.5h-3z"/><path d="M25 2l1.2-1.8"/></g></svg>

  <div class="channels">
    <div class="channel" style="left:70px"><div class="ring"><svg viewBox="0 0 11 11"><g fill="none" stroke="#d52129" stroke-width=".7"><path d="M5.5 10s3.5-3.6 3.5-6a3.5 3.5 0 0 0-7 0c0 2.4 3.5 6 3.5 6z"/><circle cx="5.5" cy="4" r="1.2"/></g></svg></div><h4>Location</h4><p>820 Maple Crest Ave #14,<br>Fairview TX 70010,</p></div>
    <div class="channel" style="left:156px"><div class="ring"><svg viewBox="0 0 11 11"><g fill="none" stroke="#d52129" stroke-width=".7"><rect x="3" y="1" width="5" height="9" rx=".8"/><path d="M5 8.6h1"/></g></svg></div><h4>Phone</h4><p>(555) 014-2290</p></div>
    <div class="channel" style="left:233px"><div class="ring"><svg viewBox="0 0 11 11"><g fill="none" stroke="#d52129" stroke-width=".7"><circle cx="5.5" cy="5.5" r="4.2"/><path d="M5.5 3v2.7l1.8 1.1"/></g></svg></div><h4>Hours</h4><p>Mon - Thu10:30 - 9:00<br>Fri - Sat10:30 - 10:30<br>Sunday11:00 - 8:00</p></div>
    <div class="channel" style="left:313px"><div class="ring"><svg viewBox="0 0 11 11"><g fill="none" stroke="#d52129" stroke-width=".7"><rect x="1.5" y="3" width="8" height="5.5"/><path d="M1.5 3l4 3 4-3"/></g></svg></div><h4>Email</h4><p>info@treatloft.example</p></div>
  </div>

  <div class="map" role="img" aria-label="Street map around the shop location"></div>
  <div class="contact-box">
    <div class="info-card">
      <h3>CONTACT INFO</h3>
      <div class="name">Treat Loft</div>
      <p class="addr">820 Maple Crest Ave #14, Fairview<br>TX 70010,</p>
      <p><span class="ico"></span>(555) 014-2290</p>
      <p><span class="ico"></span>Mon - Thu10:30 - 9:00</p>
      <p>Fri - Sat10:30 - 10:30</p>
      <p>Sunday11:00 - 8:00</p>
    </div>
    <div class="form">
      <h3>GET IN TOUCH</h3>
      <div class="field">Name</div>
      <div class="field">Email Address</div>
      <div class="field">Phone No</div>
      <div class="field field--msg">Message</div>
      <div class="submit">SUBMIT</div>
    </div>
  </div>

  <div class="footer-brand" style="top:368px">Treat<br>Loft</div>
  <nav class="footer-nav" style="top:415px"><span>HOME</span><span>ABOUTUS</span><span>MENU</span><span>GIFT/PROMOTION</span><span>CONTACT US</span></nav>
  <p class="copyright" style="top:428px">Copyright © 2019. All Rights Reserved Privacy Policy | Term of Use</p>
</section>

</body>
</html>
```